The Vantor Codex Book Cover

"The Vantor Codex" is a book I wrote with the slogan "Unlock Performance, Spark Engagement: Master the Art of Building Winning Cultures in Today's Hybrid World". The book is designed around a methodology that's mine and that I attached. I would love to see the graphic of the methodology integrated in the design in a very subtle way. Use colors from the model but the book cover should be catchy, modern and engaging to the eye.
Overall the book is about three key elements towards success:
- (Self) Directions (purpose)
- Human experience (people and psychological safety)
- Maximize engagement
The methodology is a FLOW so flow is something that could be incorporated as well in the concept.
Low design quality
Managers and Teams

```html
<!DOCTYPE html>
<html lang="en">
<head>
<meta charset="utf-8">
<title>The Vantor Codex – Book Cover</title>
<link rel="stylesheet" href="https://fonts.googleapis.com/css2?family=Bebas+Neue&family=Montserrat:wght@300;400;600&display=swap">
<style>
  :root {
    --page: #ffffff;
    --cover: #0a171b;
    --accent: #29a8e0;
    --ink: #ffffff;
    --photo-top: #3d6a86;
    --photo-mid: #1e3a4d;
  }
  * { margin: 0; padding: 0; box-sizing: border-box; }
  html, body {
    width: 1200px; height: 1200px; overflow: hidden;
    background: var(--page);
  }
  .canvas { position: relative; width: 1200px; height: 1200px; }
  .cover {
    position: absolute; left: 241px; top: 60px;
    width: 724px; height: 1087px;
    background: var(--cover);
    overflow: hidden;
  }
  .cover-photo {
    position: absolute; left: 0; top: 0; width: 724px; height: 365px;
    background:
      radial-gradient(ellipse 260px 160px at 530px 190px, rgba(170,200,215,0.55), transparent 70%),
      linear-gradient(180deg, var(--photo-top) 0%, var(--photo-mid) 55%, var(--cover) 100%);
  }
  .tagline {
    position: absolute; left: 0; width: 724px; top: 368px;
    text-align: center; white-space: nowrap;
    font-family: "Bebas Neue", sans-serif;
    font-size: 36px; letter-spacing: 3px; padding-left: 3px;
    color: var(--accent); line-height: 1;
  }
  .title-the-row {
    position: absolute; top: 435px; left: 57px; width: 612px; height: 90px;
  }
  .title-rule {
    position: absolute; top: 37px; height: 6px; width: 247px; background: var(--ink);
  }
  .title-rule.left { left: 0; }
  .title-rule.right { right: 0; }
  .title-the {
    position: absolute; left: 0; width: 612px; top: 0; text-align: center;
    font-family: "Bebas Neue", sans-serif; font-size: 88px; line-height: 1;
    color: var(--ink);
  }
  .title-main {
    position: absolute; left: 0; width: 724px; text-align: center; white-space: nowrap;
    font-family: "Bebas Neue", sans-serif; line-height: 1;
  }
  .title-main.line-one { top: 486px; font-size: 244px; color: var(--accent); }
  .title-main.line-two { top: 673px; font-size: 188px; color: var(--ink); }
  .subtitle-rule {
    position: absolute; left: 102px; width: 522px; height: 1.5px;
    background: linear-gradient(90deg, transparent, var(--accent) 15%, var(--accent) 85%, transparent);
  }
  .subtitle-rule.top { top: 873px; }
  .subtitle-rule.bottom { top: 948px; }
  .subtitle {
    position: absolute; left: 0; width: 724px; top: 883px; text-align: center;
    font-family: "Montserrat", sans-serif; font-weight: 300; white-space: nowrap;
    font-size: 24.5px; line-height: 29px; color: var(--ink);
  }
  .author {
    position: absolute; left: 0; width: 724px; top: 1009px; text-align: center;
    font-family: "Montserrat", sans-serif; font-weight: 600; white-space: nowrap;
    font-size: 36px; letter-spacing: 9px; padding-left: 9px; line-height: 1;
    color: var(--accent);
  }
</style>
</head>
<body>
<div class="canvas">
  <div class="cover">
    <div class="cover-photo" role="img" aria-label="Photo of three colleagues in an office looking at a wall screen showing a colourful circular flow model"></div>

    <p class="tagline">Unlock Performance, Spark Engagement</p>

    <div class="title-the-row">
      <span class="title-rule left"></span>
      <span class="title-the">THE</span>
      <span class="title-rule right"></span>
    </div>
    <h1>
      <span class="title-main line-one">VANTOR</span>
      <span class="title-main line-two">CODEX</span>
    </h1>

    <span class="subtitle-rule top"></span>
    <p class="subtitle">MASTER THE ART OF BUILDING WINNING<br>CULTURES IN TODAY’S HYBRID WORLD</p>
    <span class="subtitle-rule bottom"></span>

    <p class="author">JOREN VALKEMA</p>
  </div>
</div>
</body>
</html>
```